Multi-Line Insurance PPC Landing Page - Conversion optimized.

We have a PPC landing page used for the general population to get an insurance quote through an agent's site.

We'd like to improve the page for PPC traffic, make it more conversion friendly.

Site should be a single long page.

We will dynamically change the form and headlines on the page depending on what insurance "line" is being called. ie, Lift, Auto, Home, Business.

The enclosed AI file has all of the raw elements we need. We're looking to enhance the design and conversion ability.

Target Market(s)

General public needed insurance services.

Industry/Entity Type

Insurance Broker

Number of Pages Required

1 page

Font styles to use
Sans Serif

Requirements
Must have
• Form, agent picture, name, address.

```html
<!DOCTYPE html>
<html lang="en">
<head>
<meta charset="utf-8">
<title>Insurance Agent – Get an Instant Quote</title>
<link href="https://fonts.googleapis.com/css2?family=Roboto:wght@400;500;700&display=swap" rel="stylesheet">
<style>
:root{
  --blue:#1d4f9c;
  --blue-dark:#163f7e;
  --green:#1f7a23;
  --text:#444;
  --muted:#777;
  --line:#d7d7d7;
  --panel:#f2f2f2;
  --white:#fff;
}
*{box-sizing:border-box;margin:0;padding:0}
html,body{width:1200px;height:2312px;overflow:hidden}
body{font-family:"Roboto",Arial,sans-serif;color:var(--text);background:var(--white)}
section,header,footer{position:relative;width:1200px}

/* header */
.site-header{height:52px;display:flex;align-items:center;justify-content:space-between;padding:0 110px;border-bottom:1px solid var(--line)}
.brand{font-size:30px;font-weight:700;color:var(--blue)}
.brand span{color:#555;font-weight:700}
.header-phone{display:flex;align-items:center;gap:10px;color:var(--blue)}
.header-phone small{display:block;font-size:11px;color:var(--muted)}
.header-phone strong{font-size:19px;font-weight:700}

/* hero */
.hero{height:548px;overflow:hidden}
.hero-visual{position:absolute;inset:0;background:radial-gradient(ellipse at 52% 20%,#e7eef5 0%,#c7d3de 55%,#9fb0c0 100%)}
.hero-title{position:absolute;top:275px;width:100%;text-align:center;font-size:44px;font-weight:700;color:var(--blue)}
.btn{display:inline-block;background:var(--green);color:var(--white);font-weight:700;text-transform:uppercase;border-radius:2px}
.hero .btn{position:absolute;top:345px;left:528px;font-size:17px;padding:12px 22px}
.hero-arrow{position:absolute;top:278px;width:22px;height:34px;background:rgba(255,255,255,.85);display:flex;align-items:center;justify-content:center}
.hero-arrow.prev{left:10px}.hero-arrow.next{right:10px}

/* quote */
.quote{height:400px;background:var(--panel);padding-top:20px}
.agent-card{position:absolute;left:110px;top:20px;width:230px;height:360px;background:var(--white);border:1px solid var(--line);text-align:center;padding-top:24px}
.agent-photo{width:104px;height:130px;margin:0 auto;background:linear-gradient(#d9dee4,#8a97a6)}
.agent-name{margin-top:22px;font-size:17px;font-weight:500;color:#333}
.agent-phone{margin-top:8px;font-size:14px;color:#333;display:flex;justify-content:center;gap:6px;align-items:center}
.agent-address{margin-top:16px;font-size:13px;line-height:1.5;color:#555}
.quote-form{position:absolute;left:470px;top:20px;width:620px}
.quote-form h2{font-size:22px;font-weight:500;color:var(--blue);margin-bottom:14px}
.quote-form h2 b{font-weight:700}
.form-grid{display:grid;grid-template-columns:290px 200px;column-gap:50px;row-gap:12px}
.field label{display:block;font-size:11px;color:#555;margin-bottom:4px}
.input{height:24px;background:var(--white);border:1px solid var(--line);font-size:11px;color:#999;padding:5px 8px;display:flex;justify-content:space-between;align-items:center}
.input::after{content:""}
.select::after{content:"▾";color:#888}
.dob{display:flex;gap:8px}.dob .input{flex:1}
.quote-form .btn{margin-top:16px;font-size:12px;padding:7px 28px}

/* headings */
.section-title{text-align:center;font-size:24px;font-weight:500;color:var(--blue);display:flex;align-items:center;justify-content:center;gap:20px}
.section-title b{font-weight:700;color:#2c2c2c}
.section-title::before,.section-title::after{content:"";width:120px;height:1px;background:var(--line)}

/* products */
.products{height:370px;padding-top:24px}
.product-grid{position:absolute;left:140px;top:70px;display:flex;gap:20px}
.product{width:220px;height:280px;background:var(--white);box-shadow:0 2px 8px rgba(0,0,0,.15);text-align:center;padding-top:24px}
.product-icon{width:74px;height:74px;border-radius:50%;background:var(--blue);margin:0 auto;display:flex;align-items:center;justify-content:center}
.product h3{margin-top:22px;font-size:18px;font-weight:700;color:#333}
.product p{margin:12px 22px 0;font-size:12px;line-height:1.5;color:#555}
.product .btn{margin-top:16px;font-size:11px;padding:6px 12px}

/* about */
.about{height:180px;padding-top:24px}
.about p{width:1000px;margin:16px auto 0;text-align:center;font-size:13px;line-height:1.6;color:#555}

/* reviews */
.reviews{height:350px;background:var(--panel);padding-top:30px}
.review-head{display:flex;justify-content:center;align-items:center;gap:24px}
.review-head .section-title::before,.review-head .section-title::after{display:none}
.circle-arrow{width:26px;height:26px;border-radius:50%;background:var(--white);border:1px solid var(--line);display:flex;align-items:center;justify-content:center}
.review-grid{position:absolute;left:130px;top:85px;display:flex;gap:40px}
.review{width:450px}
.review blockquote{position:relative;background:var(--white);border:1px solid var(--line);padding:20px 22px 20px 60px;font-size:13px;line-height:1.6;color:#555;height:130px}
.review blockquote::before{content:"\201C";position:absolute;left:16px;top:4px;font-size:56px;color:#bbb;font-family:Georgia,serif}
.reviewer{display:flex;align-items:center;gap:14px;margin:14px 0 0 20px;font-size:12px;font-weight:500;color:#333}
.reviewer-photo{width:56px;height:56px;border-radius:50%;background:linear-gradient(#cfd6de,#7f8b99);border:3px solid var(--white)}

/* companies */
.companies{height:230px;padding-top:60px}
.companies .tab-title{display:block;width:210px;margin:0 auto;text-align:center;font-size:22px;font-weight:700;color:var(--blue);border:1px solid var(--line);border-bottom:none;padding:8px 0;background:var(--white)}
.companies .rule{height:1px;background:var(--line);margin:0 110px}
.logo-row{position:absolute;left:0;top:140px;width:1200px;display:flex;align-items:center;justify-content:space-between;padding:0 60px}
.logo-row .names{display:flex;gap:80px}
.partner{font-size:24px;font-weight:700;color:#333}

/* footer */
.site-footer{height:182px;background:var(--blue);color:var(--white);text-align:center;padding-top:22px}
.site-footer h4{font-size:14px;font-weight:700}
.site-footer p{width:1000px;margin:8px auto 0;font-size:11px;line-height:1.5;opacity:.9}
.footer-bar{position:absolute;left:0;bottom:0;width:100%;height:48px;background:var(--blue-dark);display:flex;align-items:center;justify-content:space-between;padding:0 110px}
.footer-bar small{font-size:11px}
.footer-bar strong{font-size:26px;font-weight:400}
</style>
</head>
<body>

<header class="site-header">
  <div class="brand">Insurance <span>Agent</span></div>
  <div class="header-phone">
    <svg width="26" height="26" viewBox="0 0 24 24"><path fill="#1d4f9c" d="M6.6 10.8a15 15 0 0 0 6.6 6.6l2.2-2.2c.3-.3.7-.4 1-.2 1.1.4 2.3.6 3.6.6.6 0 1 .4 1 1V20c0 .6-.4 1-1 1A17 17 0 0 1 3 4c0-.6.4-1 1-1h3.5c.6 0 1 .4 1 1 0 1.3.2 2.5.6 3.6.1.3 0 .7-.2 1z"/></svg>
    <div><small>Get a quote quickly by phone</small><strong>(555) 010-2400</strong></div>
  </div>
</header>

<section class="hero">
  <div class="hero-visual" role="img" aria-label="Photo of a field of grey umbrellas with one red umbrella standing out"></div>
  <h1 class="hero-title">Business Insurance</h1>
  <a class="btn">Get a Quote!</a>
  <span class="hero-arrow prev"><svg width="10" height="14"><path d="M8 1 2 7l6 6" stroke="#555" stroke-width="2" fill="none"/></svg></span>
  <span class="hero-arrow next"><svg width="10" height="14"><path d="m2 1 6 6-6 6" stroke="#555" stroke-width="2" fill="none"/></svg></span>
</section>

<section class="quote">
  <aside class="agent-card">
    <div class="agent-photo" role="img" aria-label="Portrait photo of the agent in a dark suit"></div>
    <div class="agent-name">Nolan Pierce - Agent</div>
    <div class="agent-phone"><svg width="14" height="14" viewBox="0 0 24 24"><path fill="#1d4f9c" d="M6.6 10.8a15 15 0 0 0 6.6 6.6l2.2-2.2c.3-.3.7-.4 1-.2 1.1.4 2.3.6 3.6.6.6 0 1 .4 1 1V20c0 .6-.4 1-1 1A17 17 0 0 1 3 4c0-.6.4-1 1-1h3.5c.6 0 1 .4 1 1 0 1.3.2 2.5.6 3.6.1.3 0 .7-.2 1z"/></svg>(555) 010-2400</div>
    <div class="agent-address">4120 Harbor Ave<br>Westfield, CA 90000</div>
  </aside>

  <form class="quote-form">
    <h2>Get An Instant <b>Insurance Quote.</b></h2>
    <div class="form-grid">
      <div class="field"><label>First Name :</label><div class="input"></div></div>
      <div class="field"><label>Height/Weight :</label><div class="input"></div></div>
      <div class="field"><label>Sex :</label><div class="input select">Select</div></div>
      <div class="field"><label>Tobacco Use :</label><div class="input select">Select</div></div>
      <div class="field"><label>Date of Birth :</label><div class="dob"><div class="input select">Month</div><div class="input select">Day</div><div class="input select">Year</div></div></div>
      <div class="field"><label>Phone :</label><div class="input"></div></div>
      <div class="field"><label>Current Health :</label><div class="input select">Select</div></div>
      <div class="field"><label>Email :</label><div class="input"></div></div>
    </div>
    <a class="btn">Submit</a>
  </form>
</section>

<section class="products">
  <h2 class="section-title"><span>Our Insurance <b>Products</b></span></h2>
  <div class="product-grid">
    <article class="product">
      <div class="product-icon"><svg width="40" height="36" viewBox="0 0 40 36" fill="#fff"><rect x="4" y="12" width="18" height="14"/><rect x="8" y="4" width="10" height="10" fill="none" stroke="#fff" stroke-width="2"/><rect x="26" y="2" width="3" height="26"/><rect x="29" y="24" width="10" height="3"/><circle cx="9" cy="30" r="4"/><circle cx="20" cy="30" r="4"/></svg></div>
      <h3>Lift</h3>
      <p>Protect the people who count on you with simple, steady cover for the years ahead.</p>
      <a class="btn">Get a Quote</a>
    </article>
    <article class="product">
      <div class="product-icon"><svg width="40" height="32" viewBox="0 0 40 32" fill="#fff"><path d="M8 4h24l5 12v12h-5v-4H8v4H3V16z"/><path d="M10 7h20l3 8H7z" fill="#1d4f9c"/><circle cx="10" cy="20" r="2.5" fill="#1d4f9c"/><circle cx="30" cy="20" r="2.5" fill="#1d4f9c"/></svg></div>
      <h3>Auto</h3>
      <p>Stay covered on every road with flexible plans for daily drivers and family cars.</p>
      <a class="btn">Get a Quote</a>
    </article>
    <article class="product">
      <div class="product-icon"><svg width="40" height="36" viewBox="0 0 40 36" fill="#fff"><path d="M20 2 2 18h5v16h10V24h6v10h10V18h5z"/></svg></div>
      <h3>Home</h3>
      <p>Guard your house and what is inside it against fire, storms, theft and damage.</p>
      <a class="btn">Get a Quote</a>
    </article>
    <article class="product">
      <div class="product-icon"><svg width="40" height="34" viewBox="0 0 40 34" fill="#fff"><path d="M14 6V3h12v3h-3V5h-6v1z"/><rect x="2" y="7" width="36" height="25" rx="3"/><rect x="2" y="17" width="36" height="2" fill="#1d4f9c"/><rect x="17" y="15" width="6" height="6" fill="#1d4f9c"/></svg></div>
      <h3>Business</h3>
      <p>Keep your company running with cover for property, staff, liability and lost income.</p>
      <a class="btn">Get a Quote</a>
    </article>
  </div>
</section>

<section class="about">
  <h2 class="section-title"><span>About <b>Insurance</b> Agent</span></h2>
  <p>For over fifteen years our agency has helped local families and business owners find the right cover at a fair price. We compare plans from many trusted carriers, explain every option in plain words and stay with you when you need to file a claim. Whether you are buying your first car, protecting a new home or growing a company, one call gets you a clear quote and honest advice from a licensed agent who knows your area.</p>
</section>

<section class="reviews">
  <div class="review-head">
    <span class="circle-arrow"><svg width="8" height="12"><path d="M7 1 2 6l5 5" stroke="#333" stroke-width="2" fill="none"/></svg></span>
    <h2 class="section-title"><span>Our Customer <b>Review</b></span></h2>
    <span class="circle-arrow"><svg width="8" height="12"><path d="m1 1 5 5-5 5" stroke="#333" stroke-width="2" fill="none"/></svg></span>
  </div>
  <div class="review-grid">
    <figure class="review">
      <blockquote>The agent walked me through every option and found a home policy that cost less than my old one. The quote took minutes and the whole process felt easy and clear.</blockquote>
      <figcaption class="reviewer"><span class="reviewer-photo" role="img" aria-label="Customer portrait photo"></span>Mr. Elliot Marsh</figcaption>
    </figure>
    <figure class="review">
      <blockquote>When my car was damaged the claim was handled fast and with real care. I now keep my auto and business cover here and always get a friendly answer.</blockquote>
      <figcaption class="reviewer"><span class="reviewer-photo" role="img" aria-label="Customer portrait photo"></span>Mr. Elliot Marsh</figcaption>
    </figure>
  </div>
</section>

<section class="companies">
  <h2 class="tab-title">Insurance Company</h2>
  <div class="rule"></div>
  <div class="logo-row">
    <svg width="16" height="20"><path d="M14 2 4 10l10 8" stroke="#1d4f9c" stroke-width="4" fill="none"/></svg>
    <div class="names">
      <span class="partner">Ledgerly</span>
      <span class="partner">Brightfield</span>
      <span class="partner">NORVEX</span>
      <span class="partner">Stonewell</span>
      <span class="partner">Tidewater</span>
    </div>
    <svg width="16" height="20"><path d="m2 2 10 8-10 8" stroke="#1d4f9c" stroke-width="4" fill="none"/></svg>
  </div>
</section>

<footer class="site-footer">
  <h4>Disclaimer</h4>
  <p>Coverage and rates vary by state and carrier. Quotes shown are estimates and are subject to underwriting review. Policy terms, conditions and exclusions apply. Please read your policy documents carefully and contact a licensed agent with any questions about your protection.</p>
  <div class="footer-bar">
    <small>© 2016 Insurance Agent. All Rights Reserved.</small>
    <strong>Insurance Agent</strong>
  </div>
</footer>

</body>
</html>
```